Velvet Lantern rebranding my business with a new business card

I have my new logo and now I need a refresher on my business cards. I really want something fun and fresh. I like black background or anything to make the color pop.
Logo
Name: Velvet Lantern
Contact Info as stated below:
Mira Pellow
555-013-4762
Logo
Name: Velvet Lantern
Mira Pellow
555-013-4762
fb.me/VelvetLanternbyMira
Instagram: @VelvetLanternbyMira

Industry/Entity Type

Business

Contact Information for Business Card

double-sided. Logo on one side. Contact info on the other.

Requirements
Must have
• Logo
• Name: Velvet Lantern
• Contact Info as stated below:
• Mira Pellow
• 555-013-4762
• fb.me/VelvetLanternbyMira
• fb.me/VelvetLanternbyMira

```html
<!DOCTYPE html>
<html lang="en">
<head>
<meta charset="utf-8">
<title>Velvet Lantern – Business Card</title>
<link href="https://fonts.googleapis.com/css2?family=Rokkitt:wght@400;600&family=Roboto:wght@400&display=swap" rel="stylesheet">
<style>
  :root {
    --stage: #efeae4;
    --card-white: #ffffff;
    --pink-deep: #c874d0;
    --pink-mid: #f6a8b4;
    --pink-soft: #fde0e4;
    --swoosh-dark: #3c3c3c;
    --ink: #1e1e1e;
    --teal: #62cbbd;
    --logo-pink: #e58fb6;
    --logo-ring: #f2b9c9;
  }
  * { box-sizing: border-box; margin: 0; padding: 0; }
  html, body { width: 1200px; height: 911px; overflow: hidden; }
  body {
    background: var(--stage);
    position: relative;
    font-family: "Roboto", sans-serif;
  }
  .card {
    position: absolute;
    width: 540px;
    height: 309px;
    border-radius: 22px;
    overflow: hidden;
    box-shadow: 0 8px 24px rgba(0,0,0,0.18);
  }
  .card--front { left: 60px; top: 140px; background: var(--card-white); }
  .card--back  { left: 600px; top: 462px; background: var(--teal); }

  .front-swoosh { position: absolute; inset: 0; width: 100%; height: 100%; }

  .contact {
    position: absolute;
    left: 40px;
    bottom: 52px;
    color: var(--ink);
  }
  .contact__name {
    font-family: "Rokkitt", serif;
    font-weight: 600;
    font-size: 27px;
    letter-spacing: 0.5px;
    text-transform: uppercase;
    margin-bottom: 10px;
  }
  .contact__list { list-style: none; font-size: 14px; line-height: 20px; }
  .contact__item { display: flex; align-items: center; gap: 8px; }
  .contact__icon { width: 12px; height: 12px; flex: none; }

  .brand-badge {
    position: absolute;
    right: 50px;
    top: 62px;
    width: 140px;
    height: 140px;
    border-radius: 50%;
    border: 3px solid var(--logo-ring);
    display: flex;
    align-items: center;
    justify-content: center;
    text-align: center;
  }
  .brand-name {
    font-family: "Rokkitt", serif;
    font-weight: 600;
    color: var(--logo-pink);
  }
  .brand-badge .brand-name { font-size: 22px; line-height: 1.05; }

  .back-web {
    position: absolute;
    left: 36px;
    top: 26px;
    writing-mode: vertical-rl;
    font-size: 13px;
    letter-spacing: 6px;
    color: #ffffff;
  }
  .back-brand {
    position: absolute;
    left: 50%;
    top: 50%;
    transform: translate(-50%, -50%);
    font-size: 40px;
    color: #ffffff;
    white-space: nowrap;
  }
</style>
</head>
<body>
  <section class="card card--front" aria-label="Card front with contact details">
    <svg class="front-swoosh" viewBox="0 0 540 309" preserveAspectRatio="none" aria-hidden="true">
      <defs>
        <linearGradient id="pinkFade" x1="0" y1="0" x2="0" y2="1">
          <stop offset="0" stop-color="var(--pink-deep)"/>
          <stop offset="0.45" stop-color="var(--pink-mid)"/>
          <stop offset="1" stop-color="var(--pink-soft)"/>
        </linearGradient>
      </defs>
      <path d="M0 0 H250 C205 60 215 140 245 205 C265 250 210 290 120 309 H0 Z" fill="url(#pinkFade)"/>
      <path d="M262 0 C218 60 228 140 258 205 C278 250 225 292 135 309" fill="none" stroke="var(--swoosh-dark)" stroke-width="6"/>
      <path d="M272 0 C228 60 238 140 268 205 C288 250 238 294 150 309" fill="none" stroke="var(--pink-mid)" stroke-width="2"/>
    </svg>

    <div class="contact">
      <p class="contact__name">Mira Pellow</p>
      <ul class="contact__list">
        <li class="contact__item">
          <svg class="contact__icon" viewBox="0 0 12 12" aria-hidden="true"><path d="M2.5 1 L4.5 1 L5 3.5 L3.8 4.4 C4.5 6 6 7.5 7.6 8.2 L8.5 7 L11 7.5 L11 9.5 C11 10.3 10.3 11 9.5 11 C5 11 1 7 1 2.5 C1 1.7 1.7 1 2.5 1 Z" fill="var(--ink)"/></svg>
          555-013-4762
        </li>
        <li class="contact__item">
          <svg class="contact__icon" viewBox="0 0 12 12" aria-hidden="true"><circle cx="6" cy="6" r="5" fill="none" stroke="var(--ink)" stroke-width="1.4"/><path d="M1 6 H11 M6 1 C3.5 4 3.5 8 6 11 M6 1 C8.5 4 8.5 8 6 11" fill="none" stroke="var(--ink)" stroke-width="1"/></svg>
          www.velvetlantern.com
        </li>
        <li class="contact__item">
          <svg class="contact__icon" viewBox="0 0 12 12" aria-hidden="true"><rect x="1" y="1" width="10" height="10" rx="1.5" fill="var(--ink)"/></svg>
          VelvetLanternbyMira
        </li>
      </ul>
    </div>

    <div class="brand-badge">
      <span class="brand-name">Velvet<br>Lantern</span>
    </div>
  </section>

  <section class="card card--back" aria-label="Card back with brand name">
    <p class="back-web">www.velvetlantern.com</p>
    <p class="brand-name back-brand">Velvet Lantern</p>
  </section>
</body>
</html>
```